Varnex Consulting Business card design.

See our website www.varnexconsulting.example which will give you a good idea of what we are about. The font is called 'Play'.

I'd like a standout business card in keeping with the themes and branding on the website

Target Market(s)

professionals. HR directors

Industry/Entity Type

Business

Contact Information for Business Card

Varnex Consulting PO Box 3172 Merrowdale NSW 2291 1300 485 193 Gavin Threlkeld Principal email: career@varnexconsulting.example ABN: 71203948865

Font styles to use
Other font styles liked:
• Play

Requirements
Must have
• Must have same design colours and branding as website.
• On back I'd prefer a list of the things we do which appears below the name at the header on the website

```html
<!DOCTYPE html>
<html lang="en">
<head>
<meta charset="utf-8">
<title>Varnex Consulting — Business Card</title>
<link href="https://fonts.googleapis.com/css2?family=Play:wght@400;700&family=Open+Sans:wght@400;600;700&display=swap" rel="stylesheet">
<style>
  :root {
    --stage: #e9eaec;
    --navy: #0f2236;
    --navy-deep: #081522;
    --navy-soft: #1c3850;
    --accent: #3d9be0;
    --accent-line: #7cc0ee;
    --paper: #ffffff;
    --paper-shade: #eef0f2;
    --ink: #4a4f55;
    --muted: #9aa6b2;
  }
  * { box-sizing: border-box; margin: 0; padding: 0; }
  html, body { width: 1200px; height: 950px; overflow: hidden; }
  body {
    background: var(--stage);
    display: flex;
    flex-direction: column;
    align-items: center;
    justify-content: center;
    gap: 60px;
  }
  .card {
    width: 700px;
    height: 400px;
    position: relative;
    overflow: hidden;
    box-shadow: 0 10px 28px rgba(0,0,0,.22);
  }

  /* Back */
  .card--back {
    background: linear-gradient(115deg, var(--navy-deep) 0%, var(--navy) 55%, var(--navy-soft) 100%);
  }
  .card--back .brand {
    position: absolute;
    top: 150px; left: 0; right: 0;
    text-align: center;
    font-family: 'Play', sans-serif;
    font-size: 46px;
    letter-spacing: 3px;
    color: var(--accent);
  }
  .services {
    position: absolute;
    right: 40px; bottom: 40px;
    font-family: 'Open Sans', sans-serif;
    font-size: 17px;
    color: var(--muted);
    letter-spacing: .5px;
  }
  .services .sep { color: var(--accent); margin: 0 8px; }

  /* Front */
  .card--front {
    background: linear-gradient(180deg, var(--paper) 0%, var(--paper) 60%, var(--paper-shade) 100%);
  }
  .card--front .brand {
    position: absolute;
    top: 62px; left: 0; right: 0;
    text-align: center;
    font-family: 'Play', sans-serif;
    font-size: 48px;
    letter-spacing: 3px;
    color: var(--navy);
  }
  .name-band {
    position: absolute;
    top: 158px; left: 0; right: 0;
    height: 118px;
    background: var(--navy);
    border-top: 3px solid var(--accent-line);
    border-bottom: 3px solid var(--accent-line);
    display: flex;
    flex-direction: column;
    align-items: center;
    justify-content: center;
    padding-left: 160px;
  }
  .name-band .person {
    font-family: 'Open Sans', sans-serif;
    font-weight: 700;
    font-size: 28px;
    color: var(--paper);
    letter-spacing: .5px;
  }
  .name-band .role {
    font-family: 'Open Sans', sans-serif;
    font-size: 19px;
    color: var(--paper);
    margin-top: 2px;
  }
  .contact {
    position: absolute;
    top: 292px; left: 0; right: 0;
    padding-left: 120px;
    font-family: 'Open Sans', sans-serif;
    font-size: 18px;
    color: var(--ink);
    display: flex;
    flex-direction: column;
    align-items: center;
    gap: 5px;
  }
  .contact .row { display: flex; align-items: center; gap: 6px; }
  .contact .gap { margin-left: 10px; }
  .icon { width: 16px; height: 16px; fill: var(--navy); flex: none; }
</style>
</head>
<body>

  <section class="card card--back" aria-label="Business card, back">
    <div class="brand">VARNEX CONSULTING</div>
    <div class="services">Coaching<span class="sep">|</span>Leadership<span class="sep">|</span>Outplacement</div>
  </section>

  <section class="card card--front" aria-label="Business card, front">
    <div class="brand">VARNEX CONSULTING</div>
    <div class="name-band">
      <div class="person">Gavin Threlkeld</div>
      <div class="role">Principal</div>
    </div>
    <div class="contact">
      <div class="row">PO Box 3172 Merrowdale NSW 2291</div>
      <div class="row">
        <svg class="icon" viewBox="0 0 16 16" aria-hidden="true"><path d="M3.5 1.5l2.5 0 1 3.2-1.6 1.2a8 8 0 0 0 4.7 4.7l1.2-1.6 3.2 1v2.5c0 .8-.7 1.5-1.5 1.5A12.5 12.5 0 0 1 2 3c0-.8.7-1.5 1.5-1.5z"/></svg>
        1300 485 193
        <svg class="icon gap" viewBox="0 0 16 16" aria-hidden="true"><path d="M1 3h14v10H1z M1.5 3.5L8 9l6.5-5.5" stroke="#fff" stroke-width="1"/></svg>
        career@varnexconsulting.example
      </div>
      <div class="row">
        <svg class="icon" viewBox="0 0 16 16" aria-hidden="true"><circle cx="8" cy="8" r="7"/><path d="M1 8h14M8 1c-3 3.5-3 10.5 0 14M8 1c3 3.5 3 10.5 0 14" stroke="#fff" stroke-width="1" fill="none"/></svg>
        www.varnexconsulting.example
      </div>
    </div>
  </section>

</body>
</html>
```